Meridale Bed Company Needs Business Card

Looking for a very nice looking business card. Creative but not extravagant. We sell beds and pillows across the U.S. and need something professional but catchy. I have attached the logo.

Name : Devin Holt
Title : President
Phone : (800) 471-2960
Email: sleep@quilmora.com
Website: www.quilmora.com

Can be single-sided or double-sided
horizontal or vertical

Can use Blues/Greys

Target Market(s)

Mass Market

Industry/Entity Type

Retail

Contact Information for Business Card

Name : Devin Holt
Title : President
Phone : (800) 471-2960
Email: sleep@quilmora.com
Website: www.quilmora.com

Requirements
Must have
• Clean, Modern, Smooth
• Can use Blues/Greys
• On the other side without the information - have something simple like www.quilmora.com or our logo
Nice to have
• Surprise me
Should not have
• Nothing crazy, nothing cluttered

```html
<!DOCTYPE html>
<html lang="en">
<head>
<meta charset="utf-8">
<title>Meridale Bed Company – Business Card</title>
<link href="https://fonts.googleapis.com/css2?family=Montserrat:wght@300;400;600;700&display=swap" rel="stylesheet">
<style>
  :root {
    --canvas: #2b2b2d;
    --card: #000000;
    --accent: #29a8dc;
    --white: #ffffff;
    --muted: #d9d9d9;
  }
  * { margin: 0; padding: 0; box-sizing: border-box; }
  html, body { width: 1200px; height: 900px; overflow: hidden; background: var(--canvas); font-family: "Montserrat", sans-serif; }
  .canvas { position: relative; width: 1200px; height: 900px; }
  .card { position: absolute; width: 665px; height: 380px; background: var(--card); border-radius: 22px; overflow: hidden; }
  .card svg.shapes { position: absolute; inset: 0; width: 100%; height: 100%; }
  .card-front { left: 110px; top: 40px; }
  .card-back { left: 425px; top: 480px; }
  .wordmark { position: absolute; color: var(--accent); font-weight: 300; letter-spacing: 1px; line-height: 1; }
  .card-front .wordmark { left: 0; right: 0; top: 118px; text-align: center; font-size: 108px; }
  .card-back .wordmark { left: 48px; top: 92px; font-size: 80px; }
  .front-url { position: absolute; left: 40px; bottom: 22px; color: var(--white); font-size: 19px; font-weight: 400; letter-spacing: 0.5px; }
  .person { position: absolute; right: 48px; top: 76px; text-align: right; }
  .person-name { color: var(--accent); font-weight: 700; font-size: 27px; line-height: 1.1; }
  .person-title { color: var(--white); font-weight: 400; font-size: 15px; }
  .contacts { position: absolute; left: 150px; top: 296px; list-style: none; }
  .contacts li { display: flex; align-items: center; gap: 9px; color: var(--white); font-size: 16px; line-height: 1.3; }
  .contacts svg { width: 12px; height: 12px; flex: none; }
</style>
</head>
<body>
<main class="canvas">

  <section class="card card-front" aria-label="Card front">
    <svg class="shapes" viewBox="0 0 665 380" aria-hidden="true">
      <polygon points="380,380 665,310 665,345 500,380" fill="var(--white)"/>
      <polygon points="0,318 320,318 355,335 355,380 0,380" fill="var(--accent)"/>
    </svg>
    <div class="wordmark">quilmora</div>
    <div class="front-url">www.quilmora.com</div>
  </section>

  <section class="card card-back" aria-label="Card back">
    <svg class="shapes" viewBox="0 0 665 380" aria-hidden="true">
      <line x1="628" y1="128" x2="135" y2="288" stroke="var(--accent)" stroke-width="2.5"/>
      <polygon points="565,238 665,205 665,275 540,318" fill="var(--accent)"/>
      <polygon points="205,380 540,318 540,338 300,380" fill="var(--white)"/>
    </svg>
    <div class="wordmark">quilmora</div>
    <div class="person">
      <div class="person-name">Devin Holt</div>
      <div class="person-title">President</div>
    </div>
    <ul class="contacts">
      <li><svg viewBox="0 0 12 12"><path d="M2.5 1l2 2.2-1 1.3c.7 1.5 1.8 2.6 3.3 3.3l1.3-1 2.2 2-1.2 1.6C5 10 2 7 1 2.2z" fill="var(--accent)"/></svg>(800) 471-2960</li>
      <li><svg viewBox="0 0 12 12"><rect x="1" y="2.5" width="10" height="7" fill="none" stroke="var(--accent)" stroke-width="1.3"/><path d="M1 2.5l5 4 5-4" fill="none" stroke="var(--accent)" stroke-width="1.3"/></svg>sleep@quilmora.com</li>
      <li><svg viewBox="0 0 12 12"><circle cx="6" cy="6" r="5" fill="none" stroke="var(--accent)" stroke-width="1.3"/><path d="M1 6h10M6 1c-2.5 3-2.5 7 0 10M6 1c2.5 3 2.5 7 0 10" fill="none" stroke="var(--accent)" stroke-width="1"/></svg>www.quilmora.com</li>
    </ul>
  </section>

</main>
</body>
</html>
```